Homeowners Insurance Provider Website

We are selling homeowners insurance policy / tenants Policy/Flood Insurance in USA in few states and planning expand nationally.

Our target audience are two folds: Customers (Buy policies) and Insurance Agents who wants to work with us to sell our policies to customers. But website should focus 80% on customers and 20% on agents. So, more customer focused user experience. Please note that there is no direct buy option for customers. They always go through insurance agents.

Customer focused, educational that makes buyer journey easy. We don’t want to come off as trying sell something as there is no direct sales involved from website.

Target Market(s)

Homeowners in USA and Insurance agent who sells these insurance.

Industry/Entity Type

Insurance

Number of Pages Required

4 page

Font styles to use
Other font styles liked:
• Open to suggestions

Colors

Designer to choose colors to be used in the design.

Requirements
Must have
• Three most important things: Trustworthy, Authentic, Simple
• Please use colors form logo and grays
• We like: www.hollowmere.com
• https://www.quillfenbrook.com/
• We need Agent Look up tool on home page similar to what is shown on example sites.
• Design:
• Home Page - Open to Ideas
• Insurance (Products) Landing Page - Info similar to: https://www.quillfenbrook.com/insurance/
• Agents Page - https://www.quillfenbrook.com/agents/
• Claims Page - Information similar to: https://www.quillfenbrook.com/claims-center/
• Site Navigation:
• Home
• Insurance
• Claims
• Agents
• About Us
• Contact Us
Nice to have
• Elegant, minimal and clean design that reflects trust and authenticity.
Should not have
• Slider or rotating images - prefer flat design. Not over powering design.

```html
<!DOCTYPE html>
<html lang="en">
<head>
<meta charset="utf-8">
<title>Hearthline Insurance Co.</title>
<link rel="stylesheet" href="https://fonts.googleapis.com/css2?family=Open+Sans:wght@400;600;700&family=Raleway:wght@400;500;600;700;800&display=swap">
<style>
:root{
  --red:#e52330;
  --navy:#233c7d;
  --navy-deep:#172a5a;
  --ink:#222;
  --body:#444;
  --grey-bg:#f3f3f4;
  --line:#c9ccd3;
  --footer:#1d1d1e;
  --white:#fff;
}
*{box-sizing:border-box;margin:0;padding:0}
html,body{width:1200px;height:2903px;overflow:hidden}
body{position:relative;font-family:"Open Sans",sans-serif;color:var(--body);background:var(--white)}
.abs{position:absolute}
.btn{position:absolute;display:flex;align-items:center;justify-content:center;font:600 12px "Open Sans",sans-serif;color:var(--white);text-transform:uppercase;letter-spacing:.3px}
.btn-red{background:var(--red)}
.btn-navy{background:var(--navy)}
.btn-white{background:var(--white);color:var(--red)}

/* hero */
.hero{left:0;top:0;width:1200px;height:548px;background:linear-gradient(100deg,#4f6b3d 0%,#8b9a72 35%,#b7b8ad 55%,#8c8f84 75%,#5d7048 100%)}
.site-header{left:141px;top:35px;width:918px;height:85px;background:rgba(255,255,255,.82);border-radius:4px}
.brand{left:18px;top:24px;display:flex;align-items:center;gap:12px;font:700 24px/1 "Raleway",sans-serif;color:var(--navy);letter-spacing:.5px}
.brand-mark{width:34px;height:34px;background:var(--navy)}
.main-nav{right:22px;top:31px;display:flex;align-items:center;gap:15px;font:500 13px "Raleway",sans-serif;color:#222}
.main-nav .active{color:var(--red)}
.main-nav .quote{background:var(--navy);color:#fff;padding:7px 9px}
.hero-card{left:141px;top:269px;width:492px;height:143px;background:rgba(255,255,255,.72);border-radius:6px;padding:18px 18px}
.hero-card h1{font:700 26px/33px "Open Sans",sans-serif;color:#1b1b1b;text-transform:uppercase}
.hero-more{left:164px;top:399px;width:104px;height:28px}

/* policy circles */
.policy{position:absolute;top:470px;width:190px;text-align:center}
.policy-circle{width:156px;height:156px;margin:0 auto;border-radius:50%;background:#fff;box-shadow:0 0 0 9px rgba(255,255,255,.45),0 2px 6px rgba(0,0,0,.12);display:flex;align-items:center;justify-content:center}
.policy-label{margin-top:18px;font:600 15px/21px "Raleway",sans-serif;color:var(--red);text-transform:uppercase}

/* about */
.section-title{font:500 26px "Raleway",sans-serif;color:#1d1d1d;letter-spacing:.5px}
.rule{position:absolute;height:1px;background:var(--line)}
.rule b{position:absolute;left:0;top:-2px;width:60px;height:4px;background:var(--navy)}
.about-text{left:141px;top:808px;width:616px;font:400 12.5px/22px "Open Sans",sans-serif;color:#333}
.quote-box{left:818px;top:720px;width:241px;height:282px;background:#f1f1f2;border:1px solid #dcdcdc}
.quote-box h2{height:36px;background:var(--navy);color:#fff;font:600 20px/36px "Raleway",sans-serif;text-align:center}
.field{position:absolute;left:15px;width:211px;height:30px;background:#eceef0;border:1px solid #d5d7da;font:400 11px/28px "Open Sans",sans-serif;color:#777;padding-left:9px}

/* split band */
.split-left{left:0;top:1058px;width:600px;height:328px;background:var(--red)}
.split-right{left:600px;top:1058px;width:600px;height:328px;background:var(--navy)}
.split h3{font:700 17px "Open Sans",sans-serif;color:#fff}
.split p{font:400 12.5px/20.5px "Open Sans",sans-serif;color:#fff}
.emblem{left:490px;top:1112px;width:220px;height:220px;border-radius:50%;background:#fff;display:flex;align-items:center;justify-content:center;text-align:center;font:700 22px/28px "Raleway",sans-serif;color:var(--navy)}

/* insurance */
.insurance{left:0;top:1386px;width:1200px;height:628px;background:var(--grey-bg)}
.card{position:absolute;top:1544px;height:412px}
.card-photo{position:absolute;inset:0}
.card-body{position:absolute;left:0;right:0;bottom:0;text-align:center;color:#fff}
.card-body h4{font:500 20px "Raleway",sans-serif}
.card-body .mini{width:56px;height:2px;background:var(--red);margin:9px auto 12px}
.card-body p{font:400 11px/19px "Open Sans",sans-serif;padding:0 26px}

/* find agent */
.agent-band{left:0;top:2014px;width:1200px;height:291px;background:var(--navy-deep)}
.agent-band h2{font:600 25px "Open Sans",sans-serif;color:#fff;text-align:center;letter-spacing:.5px}
.agent-band p{font:400 12.5px/22px "Open Sans",sans-serif;color:#fff;text-align:center}

/* claim + contact */
.claim{left:140px;top:2360px;width:300px;text-align:center}
.claim h3{font:500 24px "Raleway",sans-serif;color:var(--navy)}
.claim .big{font:800 50px/60px "Raleway",sans-serif;color:var(--red)}
.claim p{font:400 14px/22px "Raleway",sans-serif;color:var(--navy);margin-top:6px}
.cfield{position:absolute;width:258px;height:30px;border:1px solid #cfd1d5;font:400 11px/28px "Open Sans",sans-serif;color:#555;padding-left:9px}

/* footer */
.footer{left:0;top:2616px;width:1200px;height:250px;background:var(--footer);color:#ccc}
.footer h5{font:500 16px "Raleway",sans-serif;color:#fff}
.footer .fr{position:absolute;height:1px;background:#444}
.footer ul{list-style:none;font:400 11px/21.5px "Open Sans",sans-serif}
.footer li::before{content:"›";margin-right:8px;color:#888}
.footer small{font:400 11px/18px "Open Sans",sans-serif;display:block}
.bottom-bar{left:0;top:2866px;width:1200px;height:37px;background:var(--navy);color:#fff;font:600 11px/37px "Open Sans",sans-serif;padding-left:141px}
.social{position:absolute;top:10px;width:20px;height:20px;border:1px solid #fff;background:#2f57a6}
</style>
</head>
<body>

<div class="abs hero" role="img" aria-label="Photo of a smiling family standing together under a red umbrella on a leafy suburban street"></div>

<header class="abs site-header">
  <div class="abs brand"><span class="brand-mark"></span>HEARTHLINE INSURANCE CO.</div>
  <nav class="abs main-nav">
    <span class="active">Home</span><span>About Us</span><span>Insurance</span><span>Agents</span><span>Claims</span><span>Contact Us</span><span class="quote">Get a quote</span>
  </nav>
</header>

<div class="abs hero-card"><h1>Get Homeowners Insurance Policy / Tenants Policy/ Flood Insurance in USA</h1></div>
<div class="btn btn-red hero-more">Read More</div>

<div class="policy" style="left:217px">
  <div class="policy-circle">
    <svg width="60" height="60" viewBox="0 0 60 60" fill="none" stroke="#e52330" stroke-width="3.5"><path d="M12 30 L30 14 L48 30"/><path d="M18 26 V44 H42 V26"/><path d="M24 38 L36 28"/><circle cx="25" cy="29" r="2.5" fill="#e52330"/><circle cx="35" cy="37" r="2.5" fill="#e52330"/></svg>
  </div>
  <div class="policy-label">Homeowners<br>Policy</div>
</div>
<div class="policy" style="left:505px">
  <div class="policy-circle">
    <svg width="60" height="60" viewBox="0 0 60 60"><path d="M8 30 L30 10 L52 30 H46 V50 H14 V30Z" fill="#e52330"/><circle cx="24" cy="30" r="3.5" fill="#fff"/><circle cx="36" cy="30" r="3.5" fill="#fff"/><rect x="21" y="35" width="6" height="13" fill="#fff"/><rect x="33" y="35" width="6" height="13" fill="#fff"/></svg>
  </div>
  <div class="policy-label" style="margin-top:28px">Tenants Policy</div>
</div>
<div class="policy" style="left:787px">
  <div class="policy-circle">
    <svg width="60" height="60" viewBox="0 0 60 60"><path d="M12 30 L30 14 L48 30 H43 V40 H17 V30Z" fill="#e52330"/><rect x="26" y="30" width="8" height="10" fill="#fff"/><path d="M8 45 q5 -4 10 0 t10 0 t10 0 t10 0 t6 0" stroke="#e52330" stroke-width="3" fill="none"/><path d="M8 51 q5 -4 10 0 t10 0 t10 0 t10 0 t6 0" stroke="#e52330" stroke-width="3" fill="none"/></svg>
  </div>
  <div class="policy-label" style="margin-top:28px">Flood Insurance</div>
</div>

<!-- About -->
<h2 class="abs section-title" style="left:141px;top:730px">ABOUT US</h2>
<div class="rule" style="left:141px;top:786px;width:616px"><b></b></div>
<p class="abs about-text">Lorem ipsum dolor sit amet, consectetuer adipiscing elit, sed diam nonummy nibh euismod tincidunt ut laoreet dolore magna aliquam erat volutpat. Ut wisi enim ad minim veniam, quis nostrud exerci tation ullamcorper suscipit lobortis nisl ut aliquip ex ea commodo consequat. Duis autem vel eum iriure dolor in hendrerit in vulputate velit esse molestie consequat, vel illum dolore eu feugiat nulla facilisis at vero eros et accumsan et iusto odio dignissim qui blandit praesent luptatum zzril delenit augue duis dolore te feugait nulla facilisi.</p>
<div class="btn btn-navy" style="left:141px;top:971px;width:131px;height:28px">Read More</div>

<aside class="abs quote-box">
  <h2>Get A Quote</h2>
  <div class="field" style="top:57px">Name</div>
  <div class="field" style="top:94px">Email</div>
  <div class="field" style="top:131px">Subject</div>
  <div class="field" style="top:168px;height:48px">Message</div>
  <div class="btn btn-navy" style="left:15px;top:229px;width:211px;height:30px">Submit</div>
</aside>

<!-- Customers / Agents -->
<section class="split">
  <div class="abs split-left"></div>
  <div class="abs split-right"></div>
  <h3 class="abs" style="left:141px;top:1110px">Customers</h3>
  <p class="abs" style="left:141px;top:1143px;width:330px">Lorem ipsum dolor sit amet, consectetuer adipiscing elit, sed diam nonummy nibh euismod tincidunt ut laoreet dolore magna aliquam erat volutpat. Ut wisi enim ad minim veniam, quis nostrud exerci tation ullamcorper suscipit lobortis nisl ut aliquip ex ea commodo consequat. Duis autem vel eum iriure dolor in hendrerit in vulputate velit esse molestie consequat.</p>
  <div class="btn btn-navy" style="left:141px;top:1302px;width:131px;height:28px">Learn More</div>
  <h3 class="abs" style="right:141px;top:1110px">Agents</h3>
  <p class="abs" style="left:729px;top:1143px;width:330px;text-align:right">Lorem ipsum dolor sit amet, consectetuer adipiscing elit, sed diam nonummy nibh euismod tincidunt ut laoreet dolore magna aliquam erat volutpat. Ut wisi enim ad minim veniam, quis nostrud exerci tation ullamcorper suscipit lobortis nisl ut aliquip ex ea commodo consequat. Duis autem vel eum iriure dolor in hendrerit in vulputate velit esse molestie consequat.</p>
  <div class="btn btn-red" style="left:928px;top:1302px;width:131px;height:28px">Learn More</div>
  <div class="abs emblem">HEARTHLINE<br>INSURANCE CO.</div>
</section>

<!-- Insurance -->
<div class="abs insurance"></div>
<h2 class="abs section-title" style="left:0;width:1200px;top:1433px;text-align:center">INSURANCE</h2>
<div class="rule" style="left:292px;top:1490px;width:616px"><b style="left:278px"></b></div>

<article class="card" style="left:141px;width:306px">
  <div class="card-photo" role="img" aria-label="Photo of a couple looking around a bright empty room of a new home" style="background:linear-gradient(180deg,#e4e2df 0%,#b9b3ad 45%,#3a3633 78%,#111 100%)"></div>
  <div class="card-body" style="top:232px">
    <h4>Homeowner Policy</h4><div class="mini"></div>
    <p>Lorem ipsum dolor sit amet, consectetuer adipiscing elit, sed diam nonummy nibh euismod tincidunt ut laoreet dolore magna aliquam erat volutpat.</p>
  </div>
  <div class="btn btn-red" style="left:29px;top:356px;width:109px;height:29px">Quote →</div>
  <div class="btn btn-navy" style="left:146px;top:356px;width:131px;height:29px">Read More →</div>
</article>

<article class="card" style="left:447px;width:306px">
  <div class="card-photo" role="img" aria-label="Photo of a smiling couple reviewing a policy document together" style="background:linear-gradient(180deg,#e9e6e1 0%,#c8a58a 40%,#7a6a5e 60%,#2f4d94 62%,#2a4a92 100%)"></div>
  <div class="card-body" style="top:210px;height:202px;background:rgba(40,72,150,.55)">
    <h4 style="margin-top:16px">Tenant Policy</h4><div class="mini"></div>
    <p>Lorem ipsum dolor sit amet, consectetuer adipiscing elit, sed diam nonummy nibh euismod tincidunt ut laoreet dolore magna aliquam erat volutpat.</p>
  </div>
  <div class="btn btn-red" style="left:29px;top:346px;width:109px;height:29px">Quote →</div>
  <div class="btn btn-white" style="left:146px;top:346px;width:131px;height:29px">Read More →</div>
</article>

<article class="card" style="left:753px;width:306px">
  <div class="card-photo" role="img" aria-label="Photo of a red wooden house tilted over after a flood" style="background:linear-gradient(180deg,#b9c7b2 0%,#6f7d5c 30%,#8a3b33 50%,#3a2a24 75%,#111 100%)"></div>
  <div class="card-body" style="top:232px">
    <h4>Flood Policy</h4><div class="mini"></div>
    <p>Lorem ipsum dolor sit amet, consectetuer adipiscing elit, sed diam nonummy nibh euismod tincidunt ut laoreet dolore magna aliquam erat volutpat.</p>
  </div>
  <div class="btn btn-red" style="left:29px;top:356px;width:109px;height:29px">Quote →</div>
  <div class="btn btn-navy" style="left:146px;top:356px;width:131px;height:29px">Read More →</div>
</article>

<!-- Find an agent -->
<section class="abs agent-band">
  <h2 style="margin-top:60px">FIND AN AGENT</h2>
  <div style="width:130px;height:2px;background:#fff;margin:14px auto 0;opacity:.9"></div>
  <p style="width:630px;margin:26px auto 0">Lorem ipsum dolor sit amet, consectetuer adipiscing elit, sed diam nonummy nibh euismod tincidunt ut laoreet dolore magna aliquam erat volutpat. Ut wisi enim ad minim veniam, quis nostrud exerci tation ullamcorper suscipit lobortis nisl ut aliquip ex ea commodo consequat.</p>
  <div class="abs" style="left:440px;top:221px;width:156px;height:29px;background:#fff;font:400 11px/29px 'Open Sans',sans-serif;color:#666;padding-left:8px">Search...</div>
  <div class="btn btn-red" style="left:604px;top:221px;width:156px;height:29px">Find An Agent</div>
</section>

<!-- Claim -->
<div class="abs claim">
  <h3>Report And Check</h3>
  <div class="big">A Claim</div>
  <p>Login To Report A Claim Or<br>Check Your Claim Status.</p>
</div>
<div class="btn btn-red" style="left:238px;top:2531px;width:86px;height:29px">Login</div>
<div class="abs" style="left:443px;top:2355px;width:1px;height:210px;background:#d6d6d6"></div>

<h2 class="abs section-title" style="left:484px;top:2355px;font-size:25px">CONTACT FORM</h2>
<div class="rule" style="left:484px;top:2402px;width:528px"><b style="width:64px"></b></div>
<div class="abs" style="left:484px;top:2415px;font:400 11px 'Open Sans',sans-serif;color:#444">Please fill up bellow form</div>
<div class="cfield" style="left:484px;top:2440px">Name</div>
<div class="cfield" style="left:754px;top:2440px">Email</div>
<div class="cfield" style="left:484px;top:2484px">Phone</div>
<div class="cfield" style="left:754px;top:2484px">Message</div>
<div class="btn btn-red" style="left:484px;top:2531px;width:86px;height:29px">Submit</div>

<!-- Footer -->
<footer class="abs footer">
  <h5 class="abs" style="left:159px;top:45px">Quick Links</h5>
  <div class="fr" style="left:159px;top:74px;width:100px"></div>
  <ul class="abs" style="left:159px;top:84px">
    <li style="color:#2f57a6">Home</li><li>About Us</li><li>Insurance</li><li>Agents</li><li>Claims</li><li>Contact Us</li>
  </ul>

  <h5 class="abs" style="left:338px;top:45px">Contact Detail</h5>
  <div class="fr" style="left:338px;top:74px;width:185px"></div>
  <div class="abs" style="left:338px;top:88px;width:220px">
    <small style="color:#fff;font-weight:600">Hearthline Insurance</small>
    <small>Lorem ipsum dolor sit amet, consectetur adipiscing elit, sed do eiusmod</small>
  </div>
  <div class="abs" style="left:338px;top:160px;display:flex;align-items:center;gap:12px;font:400 14px 'Open Sans',sans-serif">
    <svg width="14" height="14" viewBox="0 0 24 24"><path d="M6.6 10.8a15 15 0 0 0 6.6 6.6l2.2-2.2c.3-.3.7-.4 1-.2 1.1.4 2.3.6 3.6.6.6 0 1 .4 1 1V20c0 .6-.4 1-1 1A17 17 0 0 1 3 4c0-.6.4-1 1-1h3.5c.6 0 1 .4 1 1 0 1.3.2 2.5.6 3.6.1.3 0 .7-.2 1z" fill="#2f57a6"/></svg>123.456.7890
  </div>
  <div class="abs" style="left:338px;top:195px;display:flex;align-items:center;gap:12px;font:400 11px 'Open Sans',sans-serif">
    <svg width="14" height="11" viewBox="0 0 14 11"><rect width="14" height="11" fill="#2f57a6"/><path d="M0 0 L7 6 L14 0" stroke="#1d1d1e" fill="none"/></svg>info@hearthline.com
  </div>

  <h5 class="abs" style="left:623px;top:45px">Join Our Newsletter</h5>
  <div class="fr" style="left:623px;top:74px;width:214px"></div>
  <div class="abs" style="left:623px;top:88px;width:190px"><small>Subscribe to our Newsletter to get the latest scoop right to your inbox</small></div>
  <div class="abs" style="left:623px;top:143px;width:172px;height:29px;background:#3d3d3f;color:#ddd;font:400 11px/29px 'Open Sans',sans-serif;padding-left:10px">Enter Your Email</div>
  <div class="btn btn-red" style="left:623px;top:188px;width:93px;height:27px;text-transform:none;font-size:11px">Subscribe</div>

  <div class="abs" style="left:880px;top:70px;width:170px;text-align:center;font:700 19px/26px 'Raleway',sans-serif;color:#bdbdbd">HEARTHLINE<br>INSURANCE CO.</div>
</footer>

<div class="abs bottom-bar">© 2018 Hearthlineinsurance.com. All Rights Reserved.
  <span class="social" style="left:981px"></span>
  <span class="social" style="left:1009px"></span>
  <span class="social" style="left:1037px"></span>
</div>

</body>
</html>
```